Beauty Salon Mentor Illustration

Hi There, I'm Belinda and I'm a Beauty Salon owner mentor. We are needing 5 different illustration design for a beauty salon coaching business. The pictures will be used on our website next to a small description about our course out line.
Course and what the illustrations will be referring to below:
1. Launch Pad Parlour -Make your dream of owning a salon a reality.
Three options of start-up training and support, teaching must-know insights for beauty therapists who are ready to take the leap to salon owner and want to do it right. Whether you’ve been in the beauty industry a short time or forever, Launch Pad Parlour will set you up for salon success.

2. Chairs Filled Fast - Attract more clients with simple, strategic digital marketing. Chairs Filled Fast educates on the ins and outs of sponsored social media ads. With easy-to-follow video training, you’ll establish your online presence and increase salon bookings.
Learn how to show up on social media with effective strategies that work. Choose our Handled Entirely system, or learn to do it all with our DIY system.

3. Momentum Studio Plan - Transform your salon and your life. Our most tailored program, Momentum Studio Plan offers coaching memberships with Bloom Beauty Hub’s Founder- Belinda. With our results focused framework, you will upskill employees, improve the working environment of the salon and receive leading beauty industry training as we dive into the culture and mindset of your salon. With Belinda as your business mentor and biggest cheerleader get ready to achieve your business goals and move forward with rapid growth.

4. Revive Parlour Path - Successfully put your salon back on the map.
Step into today’s beauty landscape with optimised marketing and industry expertise. If your salon’s been open for a year or even twenty years, Revive Parlour Path will elevate your business, renew your love for your salon and set you up to generate more income. Stand out from the competition as you increase online presence, learn key business development processes and see real results.

5. Skillset Studio Plan - Successfully Upskill and Level Up Your Salon. Skillset Studio Plan offers three training options- In Salon, Online & Diploma of Beauty Therapy. Whether you have your own salon or want to become qualified, Bloom Beauty Hub’s- Skillset Studio Plan adds industry authority and brings specialist expertise to all level of beauty therapists.
Our coaching is based in Australia, aim at female beauty salon owners who are ready to take their business to the next level.

In the files below is just a picture of me so you know who i am. We are wanting the illusion to appeal to a wide audience.

I am the business and everyone i attract into our coaching program works closely with me.

Target Market(s)

Beauty Salon owners; women

Font styles to use
Sans Serif

Colors
fce8d3
fee3d4
fff5ef
fff3d1
f9bb94
fcca95

Requirements
Must have
• Must be relatable to the brief, designs must look great together on the website or separately on their own.
Nice to have
• Industry relatable, engaging to the eye.
Should not have
• i would prefer if there wasn't any words on the illusion

```html
<!DOCTYPE html>
<html lang="en">
<head>
<meta charset="utf-8">
<title>Revive Parlour Path</title>
<link href="https://fonts.googleapis.com/css2?family=Archivo+Black&family=Open+Sans:wght@400;500&display=swap" rel="stylesheet">
<style>
  :root {
    --paper: #fef4ee;
    --rose: #f07a93;
    --ink: #333333;
    --logo-grey: #7a7472;
    --art-circle: #e3d5c8;
    --art-warm: #f3e6d6;
  }
  * { margin: 0; padding: 0; box-sizing: border-box; }
  html, body { width: 1200px; height: 1200px; overflow: hidden; background: var(--paper); }
  .canvas {
    position: relative;
    width: 1200px;
    height: 1200px;
    background: var(--paper);
    font-family: "Open Sans", Arial, sans-serif;
    color: var(--ink);
  }
  .frame {
    position: absolute;
    left: 38px; top: 38px;
    width: 1124px; height: 1124px;
    border: 1.5px solid var(--rose);
    border-radius: 26px;
  }
  .brand {
    position: absolute;
    left: 84px; top: 82px;
    font-size: 20px;
    font-weight: 500;
    letter-spacing: 0.08em;
    color: var(--logo-grey);
    text-transform: uppercase;
  }
  .handle {
    position: absolute;
    right: 83px; top: 118px;
    font-size: 25px;
    color: var(--rose);
  }
  .title {
    position: absolute;
    left: 77px; top: 160px;
    width: 1046px;
    font-family: "Archivo Black", "Arial Black", sans-serif;
    font-size: 77px;
    line-height: 1;
    letter-spacing: 0.005em;
    color: var(--ink);
    white-space: nowrap;
  }
  .tagline {
    position: absolute;
    left: 82px; top: 268px;
    width: 1060px;
    font-size: 60px;
    line-height: 80px;
    color: var(--rose);
    letter-spacing: -0.005em;
  }
  .hero-art {
    position: absolute;
    left: 450px; top: 422px;
    width: 302px; height: 340px;
    border-radius: 151px 151px 12px 12px;
    background: radial-gradient(circle at 50% 45%, var(--art-warm) 0%, var(--art-circle) 70%);
  }
  .body-copy {
    position: absolute;
    left: 76px; top: 778px;
    width: 1047px;
    font-size: 27.5px;
    line-height: 46.8px;
    letter-spacing: 0.045em;
    text-align: justify;
    text-align-last: left;
    color: var(--ink);
  }
  .contact-row {
    position: absolute;
    left: 76px; top: 1088px;
    width: 1047px;
    display: flex;
    justify-content: space-between;
    align-items: center;
    font-size: 26.5px;
    color: var(--rose);
  }
  .contact-item { display: flex; align-items: center; gap: 14px; }
  .contact-item svg { flex: none; }
</style>
</head>
<body>
<main class="canvas">
  <div class="frame"></div>

  <div class="brand">Bloom Beauty Hub</div>
  <div class="handle">@bloombeautyhub</div>

  <h1 class="title">Revive Parlour Path</h1>
  <p class="tagline">Successfully put your salon back on the map.</p>

  <div class="hero-art" role="img" aria-label="Illustration of a woman holding a large number one beside a hash sign and a potted plant, on a soft beige circle"></div>

  <p class="body-copy">Step into today’s beauty landscape with optimised marketing and industry expertise. If your salon’s been open for a year or even twenty years, Revive Parlour Path will elevate your business, renew your love for your salon and set you up to generate more income. Stand out from the competition as you increase online presence, learn key business development processes and see real results.</p>

  <div class="contact-row">
    <div class="contact-item">
      <svg width="22" height="22" viewBox="0 0 24 24" aria-hidden="true"><path fill="#f07a93" d="M6.6 10.8a15.1 15.1 0 0 0 6.6 6.6l2.2-2.2a1 1 0 0 1 1-.25 11.4 11.4 0 0 0 3.6.57 1 1 0 0 1 1 1V20a1 1 0 0 1-1 1A17 17 0 0 1 3 4a1 1 0 0 1 1-1h3.5a1 1 0 0 1 1 1c0 1.25.2 2.45.57 3.57a1 1 0 0 1-.25 1z"/></svg>
      <span>(+614) 1555 0198</span>
    </div>
    <div class="contact-item">
      <svg width="24" height="18" viewBox="0 0 24 18" aria-hidden="true"><rect x="1" y="1" width="22" height="16" rx="1" fill="none" stroke="#f07a93" stroke-width="1.4"/><path d="M1 1l11 9 11-9M1 17l8-7M23 17l-8-7" fill="none" stroke="#f07a93" stroke-width="1.2"/></svg>
      <span>info@bloombeautyhub.com</span>
    </div>
    <div class="contact-item">
      <svg width="22" height="22" viewBox="0 0 24 24" aria-hidden="true"><g fill="none" stroke="#f07a93" stroke-width="1.3"><circle cx="12" cy="12" r="10.5"/><ellipse cx="12" cy="12" rx="4.5" ry="10.5"/><path d="M1.5 12h21M3 6.5h18M3 17.5h18M12 1.5v21"/></g></svg>
      <span>www.bloombeautyhub.com</span>
    </div>
  </div>
</main>
</body>
</html>
```